Kestrel Facilities Business Card Design

We would now like to design business cards with the new Kestrel Facilities logo

Target Market(s)

Professional

Industry/Entity Type

Professional services

Contact Information for Business Card

Employee name, title, phone number, email address, corporate office address and logo.

Font styles to use
Sans Serif

Colors
0054AA
0677BA
7BADD7
CADEEF
E8F1F8

Requirements
Must have
• My logo
Should not have
• any other pictures or images besides my logo

```html
<!DOCTYPE html>
<html lang="en">
<head>
<meta charset="utf-8">
<title>Kestrel Facilities Business Card</title>
<link rel="stylesheet" href="https://fonts.googleapis.com/css2?family=Montserrat:wght@500;700&family=Open+Sans:wght@400;600&display=swap">
<style>
  :root {
    --brand-deep: #0054AA;
    --brand-blue: #3378C2;
    --brand-mid: #0677BA;
    --brand-light: #7BADD7;
    --brand-pale: #CADEEF;
    --brand-mist: #E8F1F8;
    --ink: #1d1d1f;
    --swoosh: #a9abae;
    --paper: #ffffff;
    --stage: #e9ecef;
  }
  * { box-sizing: border-box; margin: 0; padding: 0; }
  html, body { width: 1200px; height: 1012px; overflow: hidden; }
  body {
    background: var(--stage);
    font-family: "Open Sans", Arial, sans-serif;
    position: relative;
  }
  .card {
    position: absolute;
    left: 250px;
    width: 700px;
    height: 400px;
    border-radius: 4px;
    box-shadow: 0 10px 30px rgba(0,0,0,.18);
    overflow: hidden;
  }
  .card-front { top: 76px; background: var(--brand-blue); display: flex; align-items: center; justify-content: center; }
  .card-back { top: 536px; background: var(--paper); }

  .wordmark {
    font-family: "Montserrat", Arial, sans-serif;
    font-weight: 700;
    letter-spacing: 2px;
    text-transform: uppercase;
    display: flex;
    align-items: center;
    gap: 16px;
  }
  .wordmark-mark { width: 40px; height: 40px; }
  .card-front .wordmark { color: var(--brand-mist); font-size: 38px; }
  .card-front .wordmark-mark { background: var(--brand-mist); }
  .card-back .wordmark {
    position: absolute; left: 54px; top: 150px;
    color: var(--brand-blue); font-size: 27px; line-height: 1.15;
  }
  .card-back .wordmark-mark { background: var(--brand-blue); width: 34px; height: 34px; }

  .divider {
    position: absolute; left: 352px; top: 62px;
    width: 2px; height: 150px; background: var(--brand-blue);
  }
  .contact { position: absolute; left: 386px; top: 64px; color: var(--ink); }
  .contact-name {
    font-family: "Montserrat", Arial, sans-serif;
    font-weight: 700; font-size: 21px; color: var(--brand-blue);
    text-transform: uppercase; letter-spacing: .3px;
  }
  .contact-title { font-size: 15px; margin-top: 2px; }
  .contact-address { font-size: 15px; line-height: 1.35; margin-top: 16px; }
  .contact-lines { list-style: none; margin-top: 16px; font-size: 15px; line-height: 1.5; }
  .contact-lines li { display: flex; align-items: center; gap: 10px; }
  .contact-icon { width: 14px; height: 14px; fill: var(--brand-blue); }

  .wave { position: absolute; inset: 0; width: 700px; height: 400px; }
  .wave-fill { fill: var(--brand-blue); }
  .wave-swoosh { fill: none; stroke: var(--swoosh); stroke-width: 8; stroke-linecap: round; }
</style>
</head>
<body>
  <section class="card card-front" aria-label="Card front">
    <div class="wordmark"><span class="wordmark-mark"></span>Kestrel Facilities</div>
  </section>

  <section class="card card-back" aria-label="Card back">
    <svg class="wave" viewBox="0 0 700 400" aria-hidden="true">
      <path class="wave-swoosh" d="M500 292 C590 268 660 236 698 180"/>
      <path class="wave-fill" d="M200 400 C260 300 400 290 540 262 C620 246 670 218 700 190 L700 400 Z"/>
    </svg>

    <div class="wordmark"><span class="wordmark-mark"></span><span>Kestrel<br>Facilities</span></div>

    <div class="divider"></div>

    <div class="contact">
      <p class="contact-name">Dana Whitcombe</p>
      <p class="contact-title">Co-Founder</p>
      <p class="contact-address">4180 N. Harbor Lane<br>Suite 210 Easton 14</p>
      <ul class="contact-lines">
        <li>
          <svg class="contact-icon" viewBox="0 0 24 24" aria-hidden="true"><path d="M6.6 10.8a15.1 15.1 0 0 0 6.6 6.6l2.2-2.2a1 1 0 0 1 1-.25 11.4 11.4 0 0 0 3.6.57 1 1 0 0 1 1 1V20a1 1 0 0 1-1 1A17 17 0 0 1 3 4a1 1 0 0 1 1-1h3.5a1 1 0 0 1 1 1c0 1.25.2 2.45.57 3.57a1 1 0 0 1-.25 1z"/></svg>
          +254-300-41729
        </li>
        <li>
          <svg class="contact-icon" viewBox="0 0 24 24" aria-hidden="true"><path d="M2 5h20v14H2z M3 6l9 7 9-7" stroke="#fff" stroke-width="1.5"/></svg>
          info@kestrelfacilities.com
        </li>
      </ul>
    </div>
  </section>
</body>
</html>
```